Website for new child psychology practice

New clinical psychology practice in NSW Australia, specialising in work with children, adolescents and families. I would like to feature the colours in the logo, which was recently designed by pixelharbor designer Odette.
I am seeking a professional looking page, which is easy to navigate and is colourful and playful but not childish.
Target Market(s)
Parents and professionals
Industry/Entity Type
Health
Coding
Coded - Design and coding required
Number of Pages Required
1 page
Font styles to use
Serif
Requirements
Must have
- Pages for 'About us' 'Services' 'Fees and information' 'Contact us'
Should not have
- Childish stock photos

```html
<!DOCTYPE html>
<html lang="en">
<head>
<meta charset="utf-8">
<title>Dr Clara Penrose – Clinical Psychologist</title>
<link rel="stylesheet" href="https://fonts.googleapis.com/css2?family=Cinzel:wght@500;600;700&family=Montserrat:wght@400;500;600&display=swap">
<style>
:root{
  --plum:#a2208f;
  --plum-dark:#8a1a7a;
  --amber:#e2862e;
  --ink:#222;
  --text:#333;
  --muted:#f1f3f4;
  --blush:#fdf0fa;
  --lilac:#f1e5f0;
  --peach:#f9e3d7;
  --black:#0b0b0b;
  --white:#fff;
}
*{box-sizing:border-box;margin:0;padding:0}
html,body{width:1200px;height:4655px;overflow:hidden}
body{position:relative;background:var(--white);font-family:"Montserrat",Arial,sans-serif;color:var(--text)}
.abs{position:absolute}
.serif{font-family:"Cinzel",Georgia,serif}
.photo{position:absolute}
.heading{position:absolute;left:0;width:1200px;text-align:center;font-family:"Cinzel",Georgia,serif;font-weight:600;font-size:34px;letter-spacing:1px;color:var(--plum)}
.heading span{color:var(--amber)}
.btn{position:absolute;border:2px solid var(--plum);border-radius:6px;background:var(--white);font-family:"Cinzel",Georgia,serif;font-weight:700;color:#333;display:flex;align-items:center;justify-content:center;letter-spacing:1px}

/* nav */
.topbar{left:0;top:0;width:1200px;height:105px;background:var(--black);z-index:2}
.brand{position:absolute;display:flex;align-items:center;gap:10px;font-family:"Cinzel",Georgia,serif;font-weight:600;white-space:nowrap}
.brand i{display:block;border-radius:50%;background:var(--plum)}
.nav{position:absolute;right:62px;top:36px;display:flex;gap:48px;font-size:16px;font-weight:500;color:var(--white);list-style:none}
.nav li:first-child{color:#e0409c}

/* hero */
.hero{left:43px;top:85px;width:1114px;height:544px;background:linear-gradient(120deg,#c9b8a6,#8f7f70 45%,#5d6a7a 80%,#b8a893)}
.hero-frame{left:229px;top:238px;width:741px;height:270px;border:2px solid var(--white)}
.hero-tag{left:0;top:412px;width:1200px;text-align:center;font-family:"Cinzel",Georgia,serif;font-weight:600;font-size:21px;color:var(--white)}

/* about */
.lead{position:absolute;left:200px;width:800px;text-align:center;font-size:16px;line-height:34px}
.card{position:absolute;background:var(--muted);padding:28px 14px}
.card h3{font-family:"Cinzel",Georgia,serif;font-weight:600;color:var(--plum);font-size:20px;margin:16px 0 12px}
.card p{font-size:15.5px;line-height:34px}

/* specialising */
.band-plum{left:0;top:1451px;width:1200px;height:343px;background:linear-gradient(180deg,var(--plum),#9a1d8a)}
.band-blush{left:0;top:1794px;width:1200px;height:338px;background:var(--blush)}
.tile{position:absolute;top:1644px;height:302px;border:5px solid var(--white);box-shadow:0 2px 8px rgba(0,0,0,.2)}
.tile-label{position:absolute;left:0;right:0;top:188px;text-align:center;font-family:"Cinzel",Georgia,serif;font-weight:600;color:var(--white);font-size:19px}
.detail{left:110px;top:2004px;width:980px;height:311px;background:var(--white);border:2px solid #e5e5e5;box-shadow:0 2px 8px rgba(0,0,0,.12)}
.detail h3{position:absolute;left:365px;top:44px;font-family:"Cinzel",Georgia,serif;font-weight:600;color:var(--plum);font-size:20px}
.detail p{position:absolute;left:365px;top:82px;width:580px;font-size:15.5px;line-height:34px}

/* team */
.member{position:absolute;top:2497px;width:233px;height:309px}
.nameplate{position:absolute;left:10px;right:10px;bottom:0;height:76px;background:var(--white);text-align:center;box-shadow:0 1px 4px rgba(0,0,0,.12)}
.nameplate b{display:block;margin-top:16px;font-family:"Cinzel",Georgia,serif;font-weight:600;color:var(--plum);font-size:17px}
.nameplate small{display:block;margin-top:6px;font-size:12px;font-weight:500}
.member-feature{background:var(--plum);color:var(--white);text-align:center}

/* testimonials */
.quote{position:absolute;width:440px}
.quote p{font-size:15.5px;line-height:34px;margin-top:12px}
.quote .meta{display:flex;justify-content:space-between;align-items:center;margin-top:4px;font-size:15px}
.stars{color:var(--amber);letter-spacing:6px;font-size:20px}

/* subscribe */
.sub-band{left:0;top:3777px;width:1200px;height:428px;background:linear-gradient(90deg,#f3ecec,#fbf8f7)}
.sub-title{left:602px;top:3888px;font-family:"Cinzel",Georgia,serif;font-weight:600;font-size:35px;line-height:50px;color:var(--plum)}
.sub-title span{color:var(--amber)}
.sub-form{left:600px;top:4024px;width:477px;height:49px;background:var(--white);border-radius:6px;box-shadow:0 1px 4px rgba(0,0,0,.12);display:flex;align-items:center}
.sub-form span{padding-left:18px;font-size:15px;flex:1}
.sub-form b{height:49px;width:172px;background:var(--plum);color:var(--white);border-radius:6px;display:flex;align-items:center;justify-content:center;font-size:21px;font-weight:600}

/* footer */
.contact{position:absolute;top:4407px;display:flex;align-items:center;gap:24px;font-size:15.5px;line-height:38px}
.contact .dot{width:46px;height:46px;border-radius:50%;background:var(--plum);display:flex;align-items:center;justify-content:center;flex:none}
.divider{position:absolute;top:4380px;width:1px;height:98px;background:#999}
.footer-links{left:0;top:4518px;width:1200px;text-align:center;font-size:16px;word-spacing:2px}
.footer-links span{margin:0 16px}
.copyright{left:0;top:4574px;width:1200px;text-align:center;font-size:14px;font-weight:500}
.copyright em{font-style:normal;color:var(--plum)}
</style>
</head>
<body>

<header class="abs topbar">
  <div class="brand" style="left:86px;top:28px;color:var(--white);font-size:26px"><i style="width:34px;height:34px"></i>Dr Clara Penrose</div>
  <ul class="nav"><li>HOME</li><li>ABOUT US</li><li>SERVICES</li><li>FEES &amp; INFORMATION</li><li>CONTACT US</li></ul>
</header>

<section>
  <div class="photo hero" role="img" aria-label="Group therapy session with adults seated in a circle"></div>
  <div class="abs hero-frame"></div>
  <div class="brand" style="left:0;width:1200px;justify-content:center;top:300px;color:var(--white);font-size:50px"><i style="width:60px;height:60px"></i>Dr Clara Penrose</div>
  <div class="abs hero-tag">WE ARE A NEW CLINICAL PSYCHOLOGY PRACTICE IN NSW AUSTRALIA</div>
</section>

<section>
  <h2 class="heading" style="top:706px">ABOUT <span>DR.CLARA PENROSE</span></h2>
  <p class="lead" style="top:768px">Sed ut perspiciatis unde omnis iste natus error sit voluptatem accusantium doloremque laudantium, totam rem aperiam, eaque.</p>
  <div class="photo" style="left:112px;top:891px;width:508px;height:345px;background:linear-gradient(135deg,#e9e6e2,#bdb4aa 50%,#8b8d99)" role="img" aria-label="Psychologist taking notes with a client"></div>
  <div class="card" style="left:504px;top:916px;width:282px;height:345px">
    <svg width="60" height="60" viewBox="0 0 60 60" fill="none" stroke="var(--plum)" stroke-width="2"><rect x="4" y="4" width="34" height="46" rx="3"/><line x1="12" y1="16" x2="30" y2="16"/><line x1="12" y1="26" x2="30" y2="26"/><line x1="12" y1="36" x2="22" y2="36"/><circle cx="44" cy="44" r="11" stroke="var(--amber)"/><circle cx="44" cy="44" r="4" stroke="var(--amber)"/></svg>
    <h3>MISSION</h3>
    <p>Sed ut perspiciatis unde omnis iste natus error sit dolorem laudantium, totam rem aperiam, eaque. Ipsa quae ab illo inventore veritatis et.</p>
  </div>
  <div class="card" style="left:806px;top:950px;width:282px;height:346px">
    <svg width="60" height="60" viewBox="0 0 60 60" fill="none" stroke="var(--plum)" stroke-width="2"><path d="M6 30 Q30 8 54 30 Q30 52 6 30Z"/><circle cx="30" cy="30" r="8"/><circle cx="30" cy="30" r="3" fill="var(--amber)" stroke="none"/></svg>
    <h3>VISION</h3>
    <p>Sed ut perspiciatis unde omnis iste natus error sit dolorem laudantium, totam rem aperiam, eaque. Ipsa quae ab illo inventore veritatis et.</p>
  </div>
  <div class="btn" style="left:520px;top:1315px;width:160px;height:48px;font-size:19px">READ MORE</div>
</section>

<section>
  <div class="abs band-plum"></div>
  <div class="abs band-blush"></div>
  <h2 class="heading" style="top:1527px;color:var(--white)">WE ARE SPECIALISING IN WORK WITH</h2>
  <div class="tile" style="left:112px;width:314px;background:linear-gradient(135deg,#efe4d8,#c9b39b 60%,#8fa57f)" role="img" aria-label="Psychologist working with a young child at a desk"></div>
  <div class="tile" style="left:445px;width:310px;background:linear-gradient(135deg,#b24aa3,#8f2c83)" role="img" aria-label="Adolescent in a counselling session">
    <svg class="abs" style="left:122px;top:92px" width="62" height="62" viewBox="0 0 62 62" fill="none" stroke="#fff" stroke-width="2"><circle cx="16" cy="14" r="6"/><circle cx="31" cy="10" r="6"/><circle cx="46" cy="14" r="6"/><path d="M8 46V28h16v18M23 42V22h16v20M38 46V28h16v18"/></svg>
    <div class="tile-label">ADOLESCENTS</div>
  </div>
  <svg class="abs" style="left:589px;top:1947px" width="22" height="12" viewBox="0 0 22 12"><path d="M0 0h22L11 12z" fill="var(--plum)"/></svg>
  <div class="tile" style="left:773px;width:315px;background:linear-gradient(135deg,#d9d7d3,#a39a92 55%,#6b7380)" role="img" aria-label="Family talking with a psychologist"></div>

  <div class="abs detail">
    <div class="photo" style="left:4px;top:4px;width:318px;height:299px;background:linear-gradient(135deg,#ece8e2,#b9aea2 55%,#6f6a68)" role="img" aria-label="Teenager speaking with a counsellor holding a clipboard"></div>
    <h3>ADOLESCENTS</h3>
    <p>Sed ut perspiciatis unde omnis iste natus error sit dolorem laudantium, totam rem aperiam, eaque. Ipsa quae ab illo inventore veritatis et quasi architecto beatae vitae dicta sunt explicabo. Nemo enim ipsam voluptatem quia voluptas sit aspernatur.</p>
    <div class="btn" style="left:810px;top:246px;width:124px;height:38px;font-size:15px">READ MORE</div>
  </div>
</section>

<section>
  <h2 class="heading" style="top:2396px">MEET <span>THE TEAM</span></h2>
  <div class="member" style="left:112px;background:linear-gradient(180deg,#cfe6ea,#a9d0d8)" role="img" aria-label="Team member portrait">
    <div class="nameplate"><b>LOREM IPSUM</b><small>CHAIR PERSON</small></div>
  </div>
  <div class="member member-feature" style="left:360px">
    <div class="brand" style="left:0;width:233px;justify-content:center;top:56px;color:var(--white);font-size:18px"><i style="width:16px;height:16px;background:var(--white)"></i>Dr Clara Penrose</div>
    <div class="serif" style="margin-top:110px;font-weight:600;font-size:18px">LOREM IPSUM</div>
    <p style="font-size:15.5px;line-height:34px;padding:12px 14px 0">Sed ut perspiciatis unde omnis iste natus error sit dolorem laudantium, totam rem aperiam,</p>
  </div>
  <div class="member" style="left:607px;background:linear-gradient(180deg,#f6d2b4,#eebf98)" role="img" aria-label="Team member portrait">
    <div class="nameplate"><b>LOREM IPSUM</b><small>CHAIR PERSON</small></div>
  </div>
  <div class="member" style="left:853px;background:linear-gradient(180deg,#7c7c7c,#5e5e5e)" role="img" aria-label="Team member portrait">
    <div class="nameplate"><b>LOREM IPSUM</b><small>CHAIR PERSON</small></div>
  </div>
  <div class="btn" style="left:538px;top:2850px;width:125px;height:38px;font-size:15px">SHOW MORE</div>
</section>

<section>
  <h2 class="heading" style="top:2966px">PEOPLE <span>ARE TALKING</span></h2>
  <div class="abs" style="left:0;top:3126px;width:593px;height:150px;background:var(--lilac)"></div>
  <div class="photo" style="left:130px;top:3074px;width:324px;height:249px;background:linear-gradient(135deg,#6b6357,#2f3b4c 55%,#1f2a38)" role="img" aria-label="Smiling client at a desk with a laptop"></div>
  <div class="quote" style="left:640px;top:3105px">
    <div class="serif" style="font-size:48px;line-height:40px;color:var(--plum);font-weight:700">&ldquo;</div>
    <p>Sed ut perspiciatis unde omnis iste natus error sit dolorem laudantium, totam rem aperiam, eaque. Ipsa quae ab illo inventore veritatis.</p>
    <div class="meta"><span class="stars">★★★★★</span><span>- LOREM IPSUM</span></div>
  </div>

  <div class="abs" style="left:607px;top:3433px;width:593px;height:150px;background:var(--peach)"></div>
  <div class="photo" style="left:743px;top:3381px;width:323px;height:249px;background:linear-gradient(135deg,#e0ddd8,#b8b1a9 55%,#6d6a6a)" role="img" aria-label="Client shaking hands across a table"></div>
  <div class="quote" style="left:112px;top:3410px">
    <div class="serif" style="font-size:48px;line-height:40px;color:var(--plum);font-weight:700">&ldquo;</div>
    <p>Sed ut perspiciatis unde omnis iste natus error sit dolorem laudantium, totam rem aperiam, eaque. Ipsa quae ab illo inventore veritatis.</p>
    <div class="meta"><span class="stars">★★★★★</span><span>- LOREM IPSUM</span></div>
  </div>
</section>

<section>
  <div class="abs sub-band"></div>
  <div class="photo" style="left:0;top:3713px;width:560px;height:492px;background:linear-gradient(180deg,#f1ece8,#ded4cc 50%,#cfc4bb)" role="img" aria-label="Smiling psychologist wearing glasses"></div>
  <h2 class="abs sub-title">SUBSCRIBE <span>NOW TO GET</span><br><span>CONSULTATION</span></h2>
  <div class="abs sub-form"><span>ENTER EMAIL ADDRESS</span><b>SUBSCRIBE</b></div>
</section>

<footer>
  <div class="brand" style="left:0;width:1200px;justify-content:center;top:4290px;color:#2a2a2a;font-size:40px"><i style="width:46px;height:46px"></i>Dr Clara Penrose</div>
  <div class="contact" style="left:154px">
    <span class="dot"><svg width="22" height="22" viewBox="0 0 24 24" fill="#fff"><path d="M12 2a7 7 0 0 0-7 7c0 5 7 13 7 13s7-8 7-13a7 7 0 0 0-7-7zm0 9.5A2.5 2.5 0 1 1 12 6.5a2.5 2.5 0 0 1 0 5z"/></svg></span>
    <span>28 HARBOUR VIEW LANE<br>WOLLONGONG NSW 2500</span>
  </div>
  <div class="divider" style="left:443px"></div>
  <div class="contact" style="left:488px;top:4410px">
    <span class="dot"><svg width="20" height="20" viewBox="0 0 24 24" fill="#fff"><path d="M6.6 10.8a15 15 0 0 0 6.6 6.6l2.2-2.2a1 1 0 0 1 1-.25 11.4 11.4 0 0 0 3.6.57 1 1 0 0 1 1 1V20a1 1 0 0 1-1 1A17 17 0 0 1 3 4a1 1 0 0 1 1-1h3.5a1 1 0 0 1 1 1c0 1.25.2 2.45.57 3.57a1 1 0 0 1-.25 1z"/></svg></span>
    <span>+61 2 5550 1234</span>
  </div>
  <div class="divider" style="left:736px"></div>
  <div class="contact" style="left:773px;top:4410px">
    <span class="dot"><svg width="20" height="20" viewBox="0 0 24 24" fill="#fff"><path d="M3 5h18v14H3zm2 2v.5l7 4.5 7-4.5V7l-7 4.5z"/></svg></span>
    <span>HELLO@CLARAPENROSE.AU</span>
  </div>
  <nav class="abs footer-links">HOME<span>|</span>ABOUT US<span>|</span>SERVICES<span>|</span>FEES &amp; INFORMATION<span>|</span>CONTACT US</nav>
  <p class="abs copyright">© 2024 <em>DR.CLARA PENROSE</em> | ALL RIGHTS RESERVED.</p>
</footer>

</body>
</html>
```